Business Card Design Project : Ridgeline Press

In preparation for market launch, Tamarind's Ridgeline Press require the development of a business card. Ridgeline Press is a Community online publishing web portal. We provide the the city of Whistler located in B.C. (Canada) business directories, News, Classified ads, News, Events and blogs etc.

The main focus of the brand is to help local businesses to corporate with their online advertisement and marketing. Meeting our clients face to face is a must (B2B).

Target Market(s)

The target market is B2B customers. Business Owners to Marketing, advertising Managers

Industry/Entity Type

Business

Requirements
Must have
• - The business card will be two sided.
the BACK side will have our logo which consist of (icon, url,slogan) submited. The logo will be middle and centred.

The FRONT side should have company details:

Company Legal Name: TAMARIND RIDGELINE MEDIA

Owen Farsk
Director of Sales & Marketing

www.tamarindridgeline.biz
owen@tamarindridgeline.biz

Phone: 604 317 8842
#2714 - 582 E. Halvern St.
Vancouver, B.C. V7K2R4 Canada
Nice to have
• - For the "FRONT" side of our business card. You can separate or re-arrange with our logo components (icon, logo,slogan). It does not have to be together.

Also our company legal name is rather long so arrange or organize the name in a way to make it shorter. Your experience and creativity will have to come in play.
Should not have
• should not have other colors beside logo color and black text (2 colors). Also nothing Three dimensional

```html
<!DOCTYPE html>
<html lang="en">
<head>
<meta charset="utf-8">
<title>Ridgeline Press – Business Card</title>
<link href="https://fonts.googleapis.com/css2?family=Source+Sans+3:wght@400;600;700&display=swap" rel="stylesheet">
<style>
  :root {
    --brand-blue: #1f7cc1;
    --ink: #1c1c1c;
    --paper: #ffffff;
    --backdrop: #e6e6e6;
    --stripe-dark: #231f20;
  }
  * { margin: 0; padding: 0; box-sizing: border-box; }
  html, body { width: 1200px; height: 412px; overflow: hidden; }
  body {
    background: var(--backdrop);
    font-family: "Source Sans 3", "Myriad Pro", Arial, sans-serif;
    position: relative;
  }
  .card {
    position: absolute;
    top: 64px;
    width: 498px;
    height: 284px;
    background: var(--paper);
    overflow: hidden;
    box-shadow: 0 1px 3px rgba(0,0,0,0.18);
  }
  .card--front { left: 74px; }
  .card--back { left: 629px; }

  .wave { position: absolute; inset: 0; width: 100%; height: 100%; }

  .brand-name {
    position: absolute;
    color: var(--brand-blue);
    font-weight: 700;
    font-size: 26px;
    line-height: 1;
    display: flex;
    align-items: center;
    gap: 9px;
    white-space: nowrap;
  }
  .brand-dot {
    width: 16px; height: 16px; border-radius: 50%;
    background: var(--brand-blue);
  }
  .brand-url {
    position: absolute;
    color: var(--ink);
    font-weight: 700;
    font-size: 19.5px;
    letter-spacing: -0.2px;
    line-height: 1;
    white-space: nowrap;
  }
  .brand-slogan {
    position: absolute;
    color: var(--brand-blue);
    font-size: 15px;
    line-height: 1;
    white-space: nowrap;
  }

  .card--front .brand-name { left: 40px; top: 46px; }
  .card--front .brand-url { left: 24px; top: 98px; }
  .card--front .brand-slogan { left: 70px; top: 116px; }

  .card--back .brand-name { left: 0; right: 0; top: 98px; justify-content: center; }
  .card--back .brand-url { left: 0; right: 0; top: 159px; text-align: center; }
  .card--back .brand-slogan { left: 0; right: 0; top: 178px; text-align: center; }

  .person {
    position: absolute; right: 15px; top: 12px; text-align: right;
    color: var(--brand-blue);
  }
  .person-name { font-size: 17px; font-weight: 700; line-height: 20px; }
  .person-title { font-size: 13px; line-height: 18px; }

  .details {
    position: absolute; right: 12px; top: 158px; text-align: right;
    color: var(--paper);
    font-size: 12.5px; line-height: 15px;
  }
  .company { font-weight: 700; font-size: 13px; margin-bottom: 19px; letter-spacing: 0.1px; }
  .contact-line { display: flex; justify-content: flex-end; align-items: center; gap: 3px; }
  .contact-line svg { width: 10px; height: 10px; fill: var(--paper); }
  .address { margin-top: 10px; padding-right: 1px; }
</style>
</head>
<body>

  <section class="card card--front">
    <svg class="wave" viewBox="0 0 525 299" preserveAspectRatio="none" aria-hidden="true">
      <path d="M0,228 C120,240 200,220 270,170 C340,120 420,75 525,70" fill="none" stroke="var(--brand-blue)" stroke-width="3"/>
      <path d="M0,250 C120,262 205,240 275,188 C345,136 425,88 525,80 L525,92 C430,100 352,148 285,198 C215,250 120,272 0,262 Z" fill="var(--stripe-dark)"/>
      <path d="M0,268 C120,280 212,255 285,205 C355,156 430,104 525,98 L525,299 L0,299 Z" fill="var(--brand-blue)"/>
    </svg>

    <div class="brand-name"><span class="brand-dot"></span>Ridgeline Press</div>
    <div class="brand-url">www.tamarindridgeline.biz</div>
    <div class="brand-slogan">Your information gateway</div>

    <div class="person">
      <div class="person-name">Owen Farsk</div>
      <div class="person-title">Director of Sales &amp; Marketing</div>
    </div>

    <div class="details">
      <div class="company">TAMARIND RIDGELINE MEDIA</div>
      <div class="contact-line">604 317 8842
        <svg viewBox="0 0 10 10" aria-label="phone"><path d="M2.2,0.8 L3.6,2.6 L2.8,3.6 C3.4,4.9 4.9,6.5 6.3,7.2 L7.3,6.4 L9.2,7.8 L8.2,9.4 C4.6,9.2 0.8,5.4 0.6,1.8 Z"/></svg>
      </div>
      <div class="contact-line">owen@tamarindridgeline.biz
        <svg viewBox="0 0 10 10" aria-label="email"><path d="M0.5,2.5 H9.5 V8.5 H0.5 Z M1.2,3.2 L5,6 L8.8,3.2 Z" fill-rule="evenodd"/></svg>
      </div>
      <div class="address">#2714 - 582 E. Halvern St.<br>Vancouver, B.C. V7K2R4 Canada</div>
    </div>
  </section>

  <section class="card card--back">
    <div class="brand-name"><span class="brand-dot"></span>Ridgeline Press</div>
    <div class="brand-url">www.tamarindridgeline.biz</div>
    <div class="brand-slogan">Your information gateway</div>
  </section>

</body>
</html>
```